Heritage Hollow Business Cards

Require a business card design. <br/><br/>Needs to include logo (either round or long version) plus these details:<br/>Maya Torvell<br/>Heritage Hollow<br/>maya@kelvadtrading.com.au<br/>02 6481 7395<br/>PO Box Glenwarra NSW 2791<br/>www.heritagehollow.com.au<br/><br/>I need in an editable format so that I can create for multiple staff members. <br/><br/>

Target Market(s)

We are an online store selling renovation products to home owners are builders. Looking for a classic classy design.

Industry/Entity Type

Home And Garden

Contact Information for Business Card

Maya Torvell
Heritage Hollow
maya@kelvadtrading.com.au
02 6481 7395
PO Box Glenwarra NSW 2791
www.heritagehollow.com.au

Colors

Designer to choose colors to be used in the design.

Requirements
Must have
• Must include Logo.

```html
<!DOCTYPE html>
<html lang="en">
<head>
<meta charset="utf-8">
<title>Heritage Hollow Business Cards</title>
<link href="https://fonts.googleapis.com/css2?family=Poppins:wght@400;500;600&display=swap" rel="stylesheet">
<style>
  :root {
    --backdrop: #3b3b3d;
    --card-white: #ffffff;
    --card-green: #5b7d6c;
    --emboss-line: #4d6d5d;
    --brand-green: #4c6e5c;
    --ink: #1f1f1f;
    --logo-ink: #2a2a2a;
  }
  * { box-sizing: border-box; margin: 0; padding: 0; }
  html, body {
    width: 1200px; height: 900px; overflow: hidden;
    background: var(--backdrop);
    font-family: "Poppins", sans-serif;
  }
  .stage { position: relative; width: 1200px; height: 900px; }
  .card {
    position: absolute; left: 250px; width: 700px; height: 400px;
    border-radius: 2px;
  }
  .card-back { top: 45px; background: var(--card-green); }
  .card-front { top: 465px; background: var(--card-white); }

  .back-mark {
    position: absolute; left: 210px; top: 60px; width: 280px; height: 280px;
    border: 2px solid var(--emboss-line); border-radius: 50%;
    display: flex; align-items: center; justify-content: center;
  }
  .back-mark .mark-name {
    color: var(--emboss-line); font-weight: 600; font-size: 34px;
    line-height: 1.05; text-align: center;
  }

  .front-mark {
    position: absolute; left: 40px; top: 85px; width: 230px; height: 230px;
    border: 2px solid var(--logo-ink); border-radius: 50%;
    display: flex; align-items: center; justify-content: center;
  }
  .front-mark .mark-name {
    color: var(--logo-ink); font-weight: 600; font-size: 30px;
    line-height: 1.05; text-align: center;
  }

  .divider {
    position: absolute; left: 318px; top: 60px; width: 3px; height: 280px;
    background: var(--brand-green);
  }
  .details { position: absolute; left: 345px; top: 62px; color: var(--ink); }
  .person { color: var(--brand-green); font-weight: 600; font-size: 19px; line-height: 1.2; }
  .company { font-size: 17px; line-height: 1.3; }
  .address { color: var(--brand-green); font-size: 18px; line-height: 1.3; margin-top: 14px; }
  .contacts { list-style: none; margin-top: 16px; }
  .contacts li {
    display: flex; align-items: center; gap: 12px;
    font-size: 18px; line-height: 1.2; margin-bottom: 10px;
  }
  .contacts svg { width: 20px; height: 20px; flex: none; fill: var(--brand-green); }
</style>
</head>
<body>
<main class="stage">
  <section class="card card-back" aria-label="Card back">
    <div class="back-mark">
      <span class="mark-name">Heritage<br>Hollow</span>
    </div>
  </section>

  <section class="card card-front" aria-label="Card front">
    <div class="front-mark">
      <span class="mark-name">Heritage<br>Hollow</span>
    </div>
    <div class="divider"></div>
    <div class="details">
      <p class="person">Maya Torvell</p>
      <p class="company">Heritage Hollow</p>
      <p class="address">PO Box<br>Glenwarra NSW 2791</p>
      <ul class="contacts">
        <li>
          <svg viewBox="0 0 24 24" aria-hidden="true"><path d="M6.6 10.8a15.1 15.1 0 0 0 6.6 6.6l2.2-2.2a1 1 0 0 1 1-.25 11.4 11.4 0 0 0 3.6.57 1 1 0 0 1 1 1V20a1 1 0 0 1-1 1A17 17 0 0 1 3 4a1 1 0 0 1 1-1h3.5a1 1 0 0 1 1 1c0 1.25.2 2.45.57 3.57a1 1 0 0 1-.25 1z"/></svg>
          <span>02 6481 7395</span>
        </li>
        <li>
          <svg viewBox="0 0 24 24" aria-hidden="true"><path d="M2 5h20v14H2z M3 6l9 7 9-7" stroke="#fff" stroke-width="1.5"/></svg>
          <span>maya@kelvadtrading.com.au</span>
        </li>
        <li>
          <svg viewBox="0 0 24 24" aria-hidden="true"><circle cx="12" cy="12" r="10"/><path d="M2 12h20M12 2c3 3 3 17 0 20M12 2c-3 3-3 17 0 20" stroke="#fff" stroke-width="1.3" fill="none"/></svg>
          <span>www.heritagehollow.com.au</span>
        </li>
      </ul>
    </div>
  </section>
</main>
</body>
</html>
```